Automotive component supplier needs a business card design

We need a business card design for our company called Velran Global Components Ltd based in the UK. We are a supplier of interior and exterior components to premium car manufacturers such as Corvel Ashby, Hadley Fenn, Marquist and Tavarelli. We would like to see a modern business card design that uses the colour blue.

Target Market(s)

Premium automotive car manufacturers.

Industry/Entity Type

Automotive

Contact Information for Business Card

Company Name : Velran Global Components Limited
Address: 17 Marlow Yard, Upper Heath, Warwick, CV31 8QL, United Kingdom
Web Address : www.velrancomponents-example.co.uk

Font styles to use
Other font styles liked:
• Helvetica

Colors
3176b5
0255a3
85acd3
cfdeed
cee9f5
85cae6
34a6d7
0692cd
9bcb3c

Requirements
Must have
• Clear company logo and a mixture of blue colours.
Nice to have
• A high quality modern image.
Should not have
• Multiple colours.

```html
<!DOCTYPE html>
<html lang="en">
<head>
<meta charset="utf-8">
<title>Velran Global Components – Business Card</title>
<link rel="stylesheet" href="https://fonts.googleapis.com/css2?family=PT+Sans:wght@400;700&display=swap">
<style>
  :root {
    --backdrop: #e8e8e6;
    --card-white: #ffffff;
    --brand-blue: #0a8fd0;
    --brand-green: #9bcb3c;
    --text-grey: #4d4d4d;
    --divider: #d6d6d6;
  }
  * { margin: 0; padding: 0; box-sizing: border-box; }
  html, body {
    width: 1200px;
    height: 987px;
    overflow: hidden;
    background: var(--backdrop);
    font-family: "PT Sans", "Helvetica Neue", Arial, sans-serif;
  }
  .card {
    position: absolute;
    left: 292px;
    width: 616px;
    height: 352px;
    overflow: hidden;
    box-shadow: 0 2px 6px rgba(0,0,0,0.18);
  }
  .card--front { top: 130px; background: var(--card-white); }
  .card--back { top: 505px; background: var(--brand-green); }

  .brand {
    position: absolute;
    text-align: center;
    font-weight: 700;
    line-height: 1;
    white-space: nowrap;
  }
  .card--front .brand {
    left: 20px;
    width: 284px;
    top: 140px;
    color: var(--brand-blue);
  }
  .brand__name { display: block; font-size: 52px; letter-spacing: 2px; }
  .brand__tagline { display: block; font-size: 13px; letter-spacing: 1.2px; margin-top: 5px; }
  .card--back .brand {
    left: 0;
    width: 616px;
    top: 114px;
    color: var(--card-white);
  }
  .card--back .brand__name { font-size: 88px; letter-spacing: 4px; }
  .card--back .brand__tagline { font-size: 21px; letter-spacing: 2px; margin-top: 8px; }

  .divider {
    position: absolute;
    left: 310px;
    top: 63px;
    width: 1px;
    height: 229px;
    background: var(--divider);
  }
  .contact {
    position: absolute;
    left: 330px;
    top: 64px;
    color: var(--text-grey);
    white-space: nowrap;
  }
  .contact__name { color: var(--brand-blue); font-size: 23px; font-weight: 700; line-height: 1.2; }
  .contact__role { color: var(--brand-green); font-size: 17px; line-height: 1.2; margin-bottom: 12px; }
  .contact__address { font-size: 16px; line-height: 21.5px; font-style: normal; margin-bottom: 8px; }
  .contact__lines { list-style: none; font-size: 14px; line-height: 23.5px; }
  .contact__lines li { display: flex; align-items: center; gap: 7px; }
  .contact__lines svg { width: 13px; height: 13px; flex: none; fill: var(--brand-blue); }

  .band { position: absolute; left: 0; bottom: 0; width: 616px; height: 24px; display: block; }

  .back-url {
    position: absolute;
    left: 0;
    width: 616px;
    top: 290px;
    text-align: center;
    color: var(--card-white);
    font-size: 14px;
    letter-spacing: 3px;
    white-space: nowrap;
  }
</style>
</head>
<body>
  <section class="card card--front">
    <div class="brand">
      <span class="brand__name">VELRAN</span>
      <span class="brand__tagline">GLOBAL COMPONENTS</span>
    </div>
    <div class="divider"></div>
    <div class="contact">
      <p class="contact__name">Dorian Pell</p>
      <p class="contact__role">CEO/Founder</p>
      <address class="contact__address">
        17 Marlow Yard, Upper Heath<br>
        Warwick, CV31 8QL<br>
        United Kingdom
      </address>
      <ul class="contact__lines">
        <li><svg viewBox="0 0 16 16" aria-hidden="true"><path d="M3.5 1 6 1.5 7 5 5.3 6.4a9 9 0 0 0 4.3 4.3L11 9l3.5 1 .5 2.5-2 2C6.5 14.5 1.5 9.5 1.5 3z"/></svg>612 555 0184</li>
        <li><svg viewBox="0 0 16 16" aria-hidden="true"><path d="M4.5 0h7A1.5 1.5 0 0 1 13 1.5v13a1.5 1.5 0 0 1-1.5 1.5h-7A1.5 1.5 0 0 1 3 14.5v-13A1.5 1.5 0 0 1 4.5 0zM5 2v10h6V2zm3 11a1 1 0 1 0 0 2 1 1 0 0 0 0-2z"/></svg>784 555 0247</li>
        <li><svg viewBox="0 0 16 16" aria-hidden="true"><path d="M1 3.5h14v9H1zm1.5 1.2v.3L8 9l5.5-4v-.3z"/></svg>dp@velrancomponents-example.co.uk</li>
        <li><svg viewBox="0 0 16 16" aria-hidden="true"><path d="M8 1a7 7 0 1 0 0 14A7 7 0 0 0 8 1zm-1 2.5c.5 1 0 2-1 2.5s-.5 2 .8 2.2 1.2 1.6.7 2.8-.3 2 .2 2.3A5.3 5.3 0 0 1 3 5a5 5 0 0 1 4-1.5zm3 .3a5.3 5.3 0 0 1 2.8 6.7c-.8-.5-1.8-.3-2.3-1.3s.8-1.8-.3-2.7-.8-1.7-.2-2.7z"/></svg>www.velrancomponents-example.co.uk</li>
      </ul>
    </div>
    <svg class="band" viewBox="0 0 616 24" aria-hidden="true">
      <polygon points="0,0 404,0 398,24 0,24" fill="var(--brand-blue)"/>
      <polygon points="410,0 616,0 616,24 404,24" fill="var(--brand-green)"/>
    </svg>
  </section>

  <section class="card card--back">
    <div class="brand">
      <span class="brand__name">VELRAN</span>
      <span class="brand__tagline">GLOBAL COMPONENTS</span>
    </div>
    <p class="back-url">www.velrancomponents-example.co.uk</p>
  </section>
</body>
</html>
```